Brackwell Exteriors Needs a New Website!

We are an exteriors company specializing in vinyl siding, Corwin Maddox siding, aluminum soffit/fascia, trough. We do new construction work as well as renovations. We also build detached garages.
You can view our current website at www.brackwellfabricators.ca
I want to completely overhaul the website.
Our services are different now as we no longer do new home construction as well as we do not do the snow clearing.
I want to focus on 2 things in particular on the website:

1/ Exterior renovations

2/ Detached Garage construction.

I have included our logo in the attached files to use as well.

Some features we would like:

1/ Be able to easily attach a video from Clipverse/Reelio to highlight a product or service
2/ Quick chat or contact button that we can talk to a potential client quickly
3/ Meet the Team page that is interesting and fresh
4/ Place for us to put in helpful exterior tips/suggestions for homeowners.

Content is not important, but looking for the best design that will attract people once they click on our page and want to renovate with us.

Target Market(s)

People looking for renovations on their home, people looking to build a detached garage.

Industry/Entity Type

Residential Construction

Number of Pages Required

5+ page

Font styles to use
Sans Serif

Requirements
Must have
• Fresh and exciting home page.

Simple design. Don't want it over complicated or too much information to confuse the potential client.

Easy way to contact us.

Meet the team page that instills confidence
Nice to have
• Colour of website to go off our logo. Doesn't need to be an exact match, but something that goes well with our blue and grey.

```html
<!DOCTYPE html>
<html lang="en">
<head>
<meta charset="utf-8">
<title>Services – Brackwell Exteriors</title>
<link href="https://fonts.googleapis.com/css2?family=Montserrat:wght@400;500;600;700;800&family=Oswald:wght@600&display=swap" rel="stylesheet">
<style>
:root{
  --blue:#0b6cbd;
  --blue-dark:#0a5aa0;
  --navy:#0e4f86;
  --ink:#111418;
  --text:#55606b;
  --page:#f4f8fb;
  --card:#ffffff;
  --panel:#dcedf8;
  --ghost:#eef2f6;
  --footer-bar:#121417;
}
*{box-sizing:border-box;margin:0;padding:0}
html,body{width:1200px;height:3293px;overflow:hidden}
body{position:relative;background:var(--page);font-family:'Montserrat',sans-serif;color:var(--ink)}
.abs{position:absolute}

/* hero */
.hero-photo{position:absolute;left:0;top:0;width:1200px;height:600px;
  clip-path:polygon(0 0,100% 0,100% 390px,0 600px);
  background:
    radial-gradient(ellipse 220px 300px at 690px 260px,rgba(214,110,60,.75),rgba(214,110,60,0) 70%),
    radial-gradient(ellipse 360px 420px at 980px 200px,rgba(235,242,246,.9),rgba(235,242,246,0) 70%),
    linear-gradient(90deg,#6c8d99 0%,#50717e 35%,#6f8f9b 55%,#cfdde3 80%,#eaf1f4 100%);}
.hero-photo::after{content:"";position:absolute;inset:0;background:linear-gradient(180deg,rgba(255,255,255,.35) 0%,rgba(255,255,255,0) 25%,rgba(20,40,55,.25) 100%)}

.logo{position:absolute;display:flex;align-items:center;gap:10px;font-weight:700;letter-spacing:.5px;text-transform:uppercase}
.logo .mark{border-radius:50%}
.logo--header{left:161px;top:26px;color:var(--blue);font-size:20px}
.logo--header .mark{width:44px;height:44px;border:3px solid var(--blue)}
.logo--footer{left:0;width:1200px;justify-content:center;top:2884px;color:#fff;font-size:30px}
.logo--footer .mark{width:70px;height:70px;border:4px solid #fff}

.nav a{position:absolute;top:38px;font-size:13.5px;font-weight:500;color:#1c2229;text-decoration:none;text-transform:uppercase}
.nav a.active{color:var(--blue);font-weight:700}
.nav-rule{left:690px;top:89px;width:348px;height:1px;background:rgba(255,255,255,.6)}
.nav-active-bar{left:688px;top:88px;width:76px;height:3px;background:var(--blue)}

.hero-title{left:162px;top:268px;font-size:39px;font-weight:700;color:#fff}
.crumb{left:162px;top:325px;font-size:12.5px;color:#fff;text-transform:uppercase}

/* section heading */
.heading{position:absolute;left:0;width:1200px;text-align:center;font-size:28px;font-weight:800;text-transform:uppercase;color:var(--ink)}
.heading span{color:var(--blue)}
.heading-rule{position:absolute;left:569px;width:62px;height:2px;background:var(--blue)}
.intro{left:220px;top:650px;width:760px;text-align:center;font-size:14px;line-height:24px;color:#333a42}

/* service cards */
.card{position:absolute;left:161px;width:877px;height:261px;background:var(--card);border-radius:6px;box-shadow:0 6px 22px rgba(40,80,120,.07)}
.card .dot{position:absolute;left:28px;top:31px;width:44px;height:44px;border-radius:50%;background:#edf0f4}
.card .icon{position:absolute;left:54px;top:50px;width:46px;height:44px;background:linear-gradient(135deg,#5a6169,#2a2f35);border-radius:4px;opacity:.85}
.card .num{position:absolute;right:24px;top:18px;font-family:'Oswald',sans-serif;font-size:56px;font-weight:600;color:var(--ghost);line-height:1}
.card h3{position:absolute;left:47px;top:115px;font-size:15.5px;font-weight:700;color:var(--navy);text-transform:uppercase;letter-spacing:.3px}
.card p{position:absolute;left:47px;top:140px;width:797px;font-size:12.5px;line-height:24.5px;color:var(--text);text-align:justify}

/* inquiry */
.blue-field{position:absolute;left:0;top:2460px;width:1200px;height:776px;background:var(--blue);
  clip-path:polygon(0 205px,100% 13px,100% 100%,0 100%)}
.blue-field::after{content:"";position:absolute;inset:0;background:linear-gradient(165deg,rgba(255,255,255,0) 40%,rgba(255,255,255,.05) 41%,rgba(255,255,255,.05) 58%,rgba(255,255,255,0) 59%,rgba(255,255,255,0) 75%,rgba(0,0,0,.04) 76%)}
.panel-shadow-2{left:174px;top:2750px;width:850px;height:20px;background:#5aa0d6;border-radius:0 0 6px 6px}
.panel-shadow-1{left:167px;top:2738px;width:864px;height:20px;background:#b8d9ef;border-radius:0 0 6px 6px}
.panel{left:160px;top:2237px;width:876px;height:504px;background:var(--panel);border-radius:6px}
.field{position:absolute;background:#fff;border:1px solid #c9d6e0;border-radius:3px;font-size:11.5px;color:#707a84;padding:16px 16px 0}
.select-chev{position:absolute;right:16px;top:17px}
.captcha{left:466px;top:2580px;width:265px;height:45px;background:#f9f9f9;border:1px solid #d3d3d3;border-radius:3px;font-size:10.5px;color:#222}
.captcha .box{position:absolute;left:9px;top:12px;width:20px;height:20px;border:2px solid #c1c1c1;border-radius:2px;background:#fff}
.captcha span{position:absolute;left:37px;top:16px}
.captcha .seal{position:absolute;right:10px;top:10px;width:24px;height:24px;border-radius:50%;background:#c9d3e2}
.submit{left:539px;top:2642px;width:122px;height:36px;background:var(--blue);border-radius:3px;color:#fff;font-size:12px;font-weight:700;text-align:center;line-height:36px;box-shadow:0 3px 8px rgba(11,108,189,.3)}
.chat{left:1112px;top:2431px;width:64px;height:64px;border-radius:50%;background:#fff;box-shadow:0 4px 14px rgba(0,0,0,.15);display:flex;align-items:center;justify-content:center}

/* footer */
.foot-nav a{position:absolute;top:2999px;font-size:14px;font-weight:500;color:#fff;text-decoration:none;text-transform:uppercase}
.foot-sep{position:absolute;top:3001px;width:1px;height:14px;background:rgba(255,255,255,.35)}
.contact{position:absolute;top:3076px;width:340px;text-align:center;color:#fff}
.contact svg{display:block;margin:0 auto}
.contact h4{margin-top:20px;font-size:14px;font-weight:700;text-transform:uppercase}
.contact p{margin-top:6px;font-size:12.5px;line-height:20px}
.bar{left:0;top:3236px;width:1200px;height:57px;background:var(--footer-bar)}
.copy{left:162px;top:3256px;font-size:12px;color:#fff}
.social{position:absolute;top:3250px;width:29px;height:29px;border-radius:50%;border:2px solid #fff}
</style>
</head>
<body>

<div class="hero-photo" role="img" aria-label="Businessman holding a white hard hat, double-exposed with a city skyline"></div>

<div class="logo logo--header"><span class="mark"></span>Brackwell Exteriors</div>

<nav class="nav">
  <a style="left:498px">Home</a>
  <a style="left:581px">About Us</a>
  <a class="active" style="left:691px">Services</a>
  <a style="left:799px">Meet the Team</a>
  <a style="left:950px">Contact Us</a>
</nav>
<div class="abs nav-rule"></div>
<div class="abs nav-active-bar"></div>

<h1 class="abs hero-title">SERVICES</h1>
<div class="abs crumb">Home - Services</div>

<h2 class="heading" style="top:588px">Our <span>Services</span></h2>
<div class="heading-rule" style="top:630px"></div>
<p class="abs intro">Lorem ipsum dolor sit amet, ipsu, ofte consectetuer adipiscing elit, sed diam nonummy nibh euismod tincidunt ut laoreet dolore magna aliquam erat volutpat Ut wisi enim...</p>

<article class="card" style="top:732px">
  <div class="dot"></div><div class="icon" role="img" aria-label="Vinyl siding panel icon"></div>
  <div class="num">01</div>
  <h3>Vinyl Siding</h3>
  <p>Lorem ipsum dolor sit amet, consectetur adipiscing elit, sed do eiusmod tempor incididunt ut labore et dolore magna aliqua. Ut enim ad minim veniam, quis nostrud exercitation ullamco laboris nisi ut aliquip ex ea commodo consequat. Duis aute irure dolor in reprehenderit in voluptate velit esse cillum dolore eu fugiat nulla pariatur. Excepteur sint occaecat cupidatat non proident, sunt in culpa qui officia deserunt mollit anim id est laborum.</p>
</article>

<article class="card" style="top:1024px">
  <div class="dot"></div><div class="icon" role="img" aria-label="Fibre cement siding icon"></div>
  <div class="num">02</div>
  <h3>Corwin Maddox Siding</h3>
  <p>Lorem ipsum dolor sit amet, consectetur adipiscing elit, sed do eiusmod tempor incididunt ut labore et dolore magna aliqua. Ut enim ad minim veniam, quis nostrud exercitation ullamco laboris nisi ut aliquip ex ea commodo consequat. Duis aute irure dolor in reprehenderit in voluptate velit esse cillum dolore eu fugiat nulla pariatur. Excepteur sint occaecat cupidatat non proident, sunt in culpa qui officia deserunt mollit anim id est laborum.</p>
</article>

<article class="card" style="top:1316px">
  <div class="dot"></div><div class="icon" role="img" aria-label="Aluminum soffit profile icon"></div>
  <div class="num">03</div>
  <h3>Aluminum Soffit</h3>
  <p>Lorem ipsum dolor sit amet, consectetur adipiscing elit, sed do eiusmod tempor incididunt ut labore et dolore magna aliqua. Ut enim ad minim veniam, quis nostrud exercitation ullamco laboris nisi ut aliquip ex ea commodo consequat. Duis aute irure dolor in reprehenderit in voluptate velit esse cillum dolore eu fugiat nulla pariatur. Excepteur sint occaecat cupidatat non proident, sunt in culpa qui officia deserunt mollit anim id est laborum.</p>
</article>

<article class="card" style="top:1608px">
  <div class="dot"></div><div class="icon" role="img" aria-label="Aluminum fascia roll icon"></div>
  <div class="num">04</div>
  <h3>Aluminum Fascia</h3>
  <p>Lorem ipsum dolor sit amet, consectetur adipiscing elit, sed do eiusmod tempor incididunt ut labore et dolore magna aliqua. Ut enim ad minim veniam, quis nostrud exercitation ullamco laboris nisi ut aliquip ex ea commodo consequat. Duis aute irure dolor in reprehenderit in voluptate velit esse cillum dolore eu fugiat nulla pariatur. Excepteur sint occaecat cupidatat non proident, sunt in culpa qui officia deserunt mollit anim id est laborum.</p>
</article>

<article class="card" style="top:1900px">
  <div class="dot"></div><div class="icon" role="img" aria-label="Eavestrough icon"></div>
  <div class="num">05</div>
  <h3>Trough</h3>
  <p>Lorem ipsum dolor sit amet, consectetur adipiscing elit, sed do eiusmod tempor incididunt ut labore et dolore magna aliqua. Ut enim ad minim veniam, quis nostrud exercitation ullamco laboris nisi ut aliquip ex ea commodo consequat. Duis aute irure dolor in reprehenderit in voluptate velit esse cillum dolore eu fugiat nulla pariatur. Excepteur sint occaecat cupidatat non proident, sunt in culpa qui officia deserunt mollit anim id est laborum.</p>
</article>

<div class="blue-field"></div>

<div class="abs panel-shadow-2"></div>
<div class="abs panel-shadow-1"></div>
<section class="abs panel"></section>

<h2 class="heading" style="top:2288px">Quick <span>Inquiry</span></h2>
<div class="heading-rule" style="top:2329px"></div>

<div class="field" style="left:204px;top:2361px;width:384px;height:42px">Name*</div>
<div class="field" style="left:608px;top:2361px;width:384px;height:42px">Phone*</div>
<div class="field" style="left:204px;top:2417px;width:384px;height:42px">Email*</div>
<div class="field" style="left:608px;top:2417px;width:384px;height:42px">Choose a Service
  <svg class="select-chev" width="10" height="6" viewBox="0 0 10 6"><path d="M1 1l4 4 4-4" fill="none" stroke="#333" stroke-width="1.3"/></svg>
</div>
<div class="field" style="left:204px;top:2473px;width:788px;height:96px">Message*</div>

<div class="abs captcha"><div class="box"></div><span>I'm not a robot</span><div class="seal"></div></div>
<div class="abs submit">SUBMIT</div>

<div class="abs chat" aria-label="Quick chat">
  <svg width="32" height="32" viewBox="0 0 32 32" fill="none" stroke="var(--blue)" stroke-width="1.8" stroke-linejoin="round">
    <path d="M13 3a10 10 0 0 0-8.6 15L3 23l5-1.4A10 10 0 1 0 13 3z"/>
    <path d="M23 12.5a8 8 0 0 1 5.6 12.3L30 29l-4.2-1.2A8 8 0 0 1 15 24"/>
    <path d="M10.5 10.5a2.5 2.5 0 1 1 3.5 2.3c-.7.4-1 .9-1 1.7"/>
    <circle cx="13" cy="17.5" r=".6" fill="var(--blue)"/>
  </svg>
</div>

<div class="logo logo--footer"><span class="mark"></span>Brackwell Exteriors</div>

<nav class="foot-nav">
  <a style="left:289px">Home</a>
  <span class="foot-sep" style="left:361px"></span>
  <a style="left:387px">About Us</a>
  <span class="foot-sep" style="left:491px"></span>
  <a style="left:516px">Services</a>
  <span class="foot-sep" style="left:617px"></span>
  <a style="left:643px">Meet the Team</a>
  <span class="foot-sep" style="left:790px"></span>
  <a style="left:817px">Contact Us</a>
</nav>

<div class="contact" style="left:87px">
  <svg width="28" height="44" viewBox="0 0 28 44" fill="none" stroke="#fff" stroke-width="1.6"><rect x="2" y="1" width="24" height="42" rx="4"/><line x1="2" y1="7" x2="26" y2="7"/><line x1="2" y1="35" x2="26" y2="35"/><circle cx="14" cy="39" r="1.6"/></svg>
  <h4>Phone</h4>
  <p>+1 780-555-0143</p>
</div>
<div class="contact" style="left:422px">
  <svg width="34" height="44" viewBox="0 0 34 44" fill="none" stroke="#fff" stroke-width="1.6"><path d="M17 43S2 25 2 16a15 15 0 0 1 30 0c0 9-15 27-15 27z"/><circle cx="17" cy="16" r="5"/></svg>
  <h4>Brackwell Exteriors</h4>
  <p>4820 Ridgeline Rd #118, Alder<br>Park, AB T8A 2K4, Canada</p>
</div>
<div class="contact" style="left:754px">
  <svg width="50" height="40" viewBox="0 0 50 40" fill="none" stroke="#fff" stroke-width="1.6"><rect x="1" y="3" width="48" height="35"/><path d="M1 3l24 20L49 3M1 38l18-16M49 38L31 22"/></svg>
  <h4>Email</h4>
  <p>hello@brackwellexteriors.ca</p>
</div>

<footer class="abs bar"></footer>
<div class="abs copy">Copyright © 2020 &nbsp;BRACKWELL EXTERIORS. All Rights Reserved.</div>
<span class="social" style="left:890px;background:#1e5aa8"></span>
<span class="social" style="left:928px;background:#1f8fd6"></span>
<span class="social" style="left:967px;background:#1a6cb0"></span>
<span class="social" style="left:1008px;background:#a83a9a"></span>

</body>
</html>
```